Redesign 2016 Digital Marketing Website and Convert to Wordpress

Technology needed to integrate:

- redesign and convert to wordpress
- gravity forms
- malware and hacker defense / honeypot (must be very secure from hackers)
- I want gravity forms to be a flow that asks many questions with icons and progress bar.
- 1 home page design
- 1 blog design
- 1 design for internal page content
- 1 multi step gravity form
I want to focus on SMB's. We are a marketing agency thats been around since 2016.

Site is: tallpine.agency

I am looking to redesign the homepage, blog page and services page. The services page will be a template for all inner pages of the site. All content needs to be moved into the new design.

I want to get ride of the weird video.

I need you to install gravity forms pro model so we can pass utms.

I need the gravity form to be a multi step form with icons.

All "contact us" or "get a free assesments" call to actions will go to this form only.

step 1:
what is your website

step 2:
what industry are you in
- option
- Home Services
- Legal
- Ecommerce
- Lead Gen

No matter which one they select its going to produce a differnt calculator for them.

Law:
How many leads did you get last month
how much is each ase worth on average
How much revenue do you want to make

Home servicse:
How many bookings did you get last month
How much is each service worht on average
How much revenue do you wangt to make

Ecommerce:
What is your average order value
How muny purchases did you have last month
How much revenue did you drive
How much revenue do you want to drive

For lead gen:
How many leads did you get lawt month
How much revenue did they generate

Step 3:
What is your current advertising budget

step 4:
Do you have a CRM and if so what is it

Step 5:
What is your personal informagtion
name
email
phone

Let me know if this is enough to get you going

Small and medium sized law firms, ecommerce, home services and lead gen customers.

We are a digital marketing agency

• Use whats on the current site and improve upon it

• Must be very secure, developed into a wordpress website. using gravity forms. remove my photo and my staffs photo, depersonalize it so it doesnt mention me or sam crolley. Use the same color scheme. I am looking to redesign the homepage, blog page and services page. The services page will be a template for all inner pages of the site. All content needs to be moved into the new design. I want to get ride of the weird video. I need you to install gravity forms pro model so we can pass utms. I need the gravity form to be a multi step form with icons. All "contact us" or "get a free assesments" call to actions will go to this form only. step 1: what is your website step 2: what industry are you in - option - Home Services - Legal - Ecommerce - Lead Gen No matter which one they select its going to produce a differnt calculator for them. Law: How many leads did you get last month how much is each ase worth on average How much revenue do you want to make Home servicse: How many bookings did you get last month How much is each service worht on average How much revenue do you wangt to make Ecommerce: What is your average order value How muny purchases did you have last month How much revenue did you drive How much revenue do you want to drive For lead gen: How many leads did you get lawt month How much revenue did they generate How much revenue do you want to make Step 3: What is your current advertising budget step 4: Do you have a CRM and if so what is it Step 5: What is your personal informagtion name email phone Let me know if this is enough to get you going
• SHOULD NOT BE SLOPPY, I AM LOOKING FOR ATTENTION TO DETAIL.

```html
<!DOCTYPE html>
<html lang="en">
<head>
<meta charset="utf-8">
<title>Tall Pine – Grow Your Revenue Form Flow</title>
<link href="https://fonts.googleapis.com/css2?family=Poppins:wght@400;500;600;700;800&display=swap" rel="stylesheet">
<style>
:root{
  --bg-maroon:#721216;
  --brand-red:#7d1518;
  --orange:#f7941d;
  --ink:#2f2f2f;
  --text:#555;
  --muted:#bdbdbd;
  --nav:#2b2b2b;
  --line:#e6e6e6;
  --white:#fff;
}
*{box-sizing:border-box;margin:0;padding:0}
html,body{width:1200px;height:870px;overflow:hidden}
body{background:var(--bg-maroon);font-family:'Poppins',sans-serif;position:relative}
.screen{position:absolute;width:711px;height:765px;background:var(--white);transform:scale(.5288);transform-origin:0 0;overflow:hidden}
.s1{left:22.7px;top:23.8px}.s2{left:416.8px;top:23.8px}.s3{left:810.4px;top:23.8px}
.s4{left:213.8px;top:444.9px}.s5{left:614.9px;top:444.9px}
.abs{position:absolute}
.brand{position:absolute;display:flex;align-items:center;gap:9px}
.brand-mark{width:36px;height:36px;border-radius:50%;background:var(--brand-red)}
.brand-name{font-size:15px;letter-spacing:1.6px;color:#4a4a4a;line-height:1}
.brand-sub{font-size:5.4px;letter-spacing:2.6px;color:#777;margin-top:4px}
.site-header .brand{left:45px;top:8px}
.call{left:334px;top:20px;font-size:10px;font-weight:700;color:#333}
.call b{color:var(--brand-red)}
.btn-orange{left:534px;top:12px;width:133px;height:29px;background:var(--orange);color:#fff;font-size:8.6px;font-weight:600;display:flex;align-items:center;justify-content:center;letter-spacing:.2px}
.main-nav{left:0;top:53px;width:711px;height:33px;background:var(--nav);display:flex;justify-content:center;align-items:center;gap:27px;padding-right:16px}
.main-nav span{color:#fff;font-size:8.2px;letter-spacing:.3px}
.form-title{left:0;top:114px;width:711px;text-align:center;font-size:21px;font-weight:700;color:var(--ink);letter-spacing:.6px}
.title-rule{left:328px;top:151px;width:55px;height:2px;background:var(--brand-red)}
.stepper{left:0;top:180px}
.step-head{left:173px;top:244px;display:flex;gap:8px;align-items:center}
.step-icon{width:26px;height:28px}
.step-label{font-size:10.5px;font-weight:700;color:var(--brand-red);line-height:1.4}
.step-q{font-size:9.6px;color:#333;line-height:1.4}
.field{position:absolute;height:30px;border:1px solid #d9d9d9;display:flex;align-items:center;justify-content:space-between;padding:0 10px 0 12px;font-size:7.2px;color:#444}
.field svg{width:9px;height:9px}
.btn-next{position:absolute;left:472px;top:284px;width:68px;height:30px;background:var(--nav);color:#fff;font-size:11px;font-weight:700;display:flex;align-items:center;justify-content:center;gap:6px}
.btn-submit{position:absolute;left:472px;top:284px;width:76px;height:66px;background:var(--orange);color:#fff;font-size:11px;font-weight:700;display:flex;align-items:center;justify-content:center;gap:6px}
.rule{left:0;width:711px;height:1px;background:var(--line)}
.site-footer .brand{left:45px;top:418px}
.partner-badge{left:247px;top:411px;width:122px;height:52px;display:flex;gap:10px}
.partner-badge i{width:13px;height:52px;background:#d93a2f;display:block}
.partner-badge em{flex:1;background:#ececec;border-radius:3px;display:block}
.listing-badge{left:407px;top:410px;width:52px;height:52px;border-radius:50%;background:#1d3f66}
.follow{left:524px;top:414px;font-size:10.5px;color:#333;letter-spacing:.4px}
.socials{left:524px;top:438px;display:flex;gap:16px}
.socials i{width:17px;height:17px;border-radius:50%;background:#333;display:block}
.cols{left:45px;top:504px;display:flex}
.col h4{font-size:13px;font-weight:700;color:#333;letter-spacing:.3px;margin-bottom:6px}
.col p{font-size:7.3px;color:#555;line-height:10.5px;margin-bottom:9px}
.c1{width:143px}.c2{width:176px}.c3{width:159px}.c4{width:150px}
.copyright{left:135px;top:733px;font-size:7.3px;color:#555}
.build{left:690px;top:734px;font-size:7.3px;color:#555}
</style>
</head>
<body>

<!-- Screen 1 -->
<section class="screen s1">
  <header class="site-header">
    <div class="brand"><div class="brand-mark"></div><div><div class="brand-name">TALL PINE</div><div class="brand-sub">GROWTH MARKETING</div></div></div>
    <div class="abs call">OR CALL US NOW : <b>(480) 555-0142</b></div>
    <div class="abs btn-orange">GROW YOUR REVENUE</div>
    <nav class="abs main-nav"><span>HOME</span><span>ABOUT</span><span>INDUSTRIES</span><span>SERVICES</span><span>BLOG</span><span>CONTACT US</span></nav>
  </header>
  <h1 class="abs form-title">GROW YOUR REVENUE NOW</h1>
  <div class="abs title-rule"></div>
  <svg class="abs stepper" width="711" height="34" viewBox="0 0 711 34" font-family="Poppins, sans-serif" font-size="13" font-weight="600" text-anchor="middle">
    <line x1="195" y1="17" x2="230" y2="17" stroke="#7d1518" stroke-width="2"/><line x1="230" y1="17" x2="516" y2="17" stroke="#ccc" stroke-width="1.2"/>
    <circle cx="178" cy="17" r="16.5" fill="#7d1518"/><text x="178" y="22" fill="#fff">1</text>
    <circle cx="267" cy="17" r="16" fill="#fff" stroke="#ccc" stroke-width="1.3"/><text x="267" y="22" fill="#bbb">2</text>
    <circle cx="356" cy="17" r="16" fill="#fff" stroke="#ccc" stroke-width="1.3"/><text x="356" y="22" fill="#bbb">3</text>
    <circle cx="444" cy="17" r="16" fill="#fff" stroke="#ccc" stroke-width="1.3"/><text x="444" y="22" fill="#bbb">4</text>
    <circle cx="533" cy="17" r="16" fill="#fff" stroke="#ccc" stroke-width="1.3"/><text x="533" y="22" fill="#bbb">5</text>
  </svg>
  <div class="abs step-head">
    <svg class="step-icon" viewBox="0 0 26 28" fill="none" stroke="#7d1518" stroke-width="1.2"><circle cx="13" cy="14" r="11"/><ellipse cx="13" cy="14" rx="5" ry="11"/><line x1="2" y1="14" x2="24" y2="14"/><rect x="3" y="11" width="20" height="6" fill="#fff"/></svg>
    <div><div class="step-label">Step 1</div><div class="step-q">What is your website</div></div>
  </div>
  <div class="field" style="left:173px;top:284px;width:293px">Enter business name<svg viewBox="0 0 10 10"><rect x="1" y="3" width="8" height="6" fill="#999"/></svg></div>
  <div class="btn-next">NEXT <svg width="6" height="8" viewBox="0 0 6 8"><path d="M1 1l3 3-3 3" stroke="#fff" fill="none"/></svg></div>
  <div class="abs rule" style="top:392px"></div>
  <footer class="site-footer">
    <div class="brand"><div class="brand-mark"></div><div><div class="brand-name">TALL PINE</div><div class="brand-sub">GROWTH MARKETING</div></div></div>
    <div class="abs partner-badge" role="img" aria-label="Partner badge"><i></i><em></em></div>
    <div class="abs listing-badge" role="img" aria-label="Review listing badge"></div>
    <div class="abs follow">FOLLOW US</div>
    <div class="abs socials" aria-label="Social links"><i></i><i></i><i></i><i></i><i></i></div>
    <div class="abs rule" style="top:481px"></div>
    <div class="abs cols">
      <div class="col c1"><h4>QUICK LINKS</h4><p>About</p><p>Industries</p><p>Services</p><p>Resources</p><p>Training</p><p>Blog</p><p>Contact Us</p></div>
      <div class="col c2"><h4>SERVICES</h4><p>Programmatic Advertising</p><p>Search Engine Marketing (SEM)</p><p>Search Engine Optimization (SEO)</p><p>Content Marketing</p><p>Email Marketing</p><p>Paid Search Advertising</p><p>Paid Social Advertising</p></div>
      <div class="col c3"><h4>INDUSTRIES</h4><p>Ecommerce</p><p>Electricians</p><p>Financial Services Marketing</p><p>Home Builders</p><p>Home Services</p><p>Hvac Companies</p><p>Cosmetic Surgery Centers</p><p>Dental Marketing</p></div>
      <div class="col c4"><h4>GUIDES</h4><p>Ultimate Guide On Growing Your<br>Medical Practice Business</p><p>Legal Marketing Strategy Guide For<br>Law Firm Offices</p><p>Ultimate Story Ads Guide To<br>Skyrocket Your Leads And Sales</p><p>Ultimate Guide To Search<br>Engine Queries</p></div>
    </div>
    <div class="abs rule" style="top:715px"></div>
    <div class="abs copyright">Copyright © 2024 CompanyName &nbsp;All Rights Reserved. Privacy Policy, Terms Of Use, Press &amp; Media, Cookie Policy</div>
    <div class="abs build">x10</div>
  </footer>
</section>

<!-- Screen 2 -->
<section class="screen s2">
  <header class="site-header">
    <div class="brand"><div class="brand-mark"></div><div><div class="brand-name">TALL PINE</div><div class="brand-sub">GROWTH MARKETING</div></div></div>
    <div class="abs call">OR CALL US NOW : <b>(480) 555-0142</b></div>
    <div class="abs btn-orange">GROW YOUR REVENUE</div>
    <nav class="abs main-nav"><span>HOME</span><span>ABOUT</span><span>INDUSTRIES</span><span>SERVICES</span><span>BLOG</span><span>CONTACT US</span></nav>
  </header>
  <h1 class="abs form-title">GROW YOUR REVENUE NOW</h1>
  <div class="abs title-rule"></div>
  <svg class="abs stepper" width="711" height="34" viewBox="0 0 711 34" font-family="Poppins, sans-serif" font-size="13" font-weight="600" text-anchor="middle">
    <line x1="195" y1="17" x2="319" y2="17" stroke="#7d1518" stroke-width="2"/><line x1="319" y1="17" x2="516" y2="17" stroke="#ccc" stroke-width="1.2"/>
    <circle cx="178" cy="17" r="16.5" fill="#7d1518"/><text x="178" y="22" fill="#fff">1</text>
    <circle cx="267" cy="17" r="16.5" fill="#7d1518"/><text x="267" y="22" fill="#fff">2</text>
    <circle cx="356" cy="17" r="16" fill="#fff" stroke="#ccc" stroke-width="1.3"/><text x="356" y="22" fill="#bbb">3</text>
    <circle cx="444" cy="17" r="16" fill="#fff" stroke="#ccc" stroke-width="1.3"/><text x="444" y="22" fill="#bbb">4</text>
    <circle cx="533" cy="17" r="16" fill="#fff" stroke="#ccc" stroke-width="1.3"/><text x="533" y="22" fill="#bbb">5</text>
  </svg>
  <div class="abs step-head">
    <svg class="step-icon" viewBox="0 0 26 28" fill="none" stroke="#7d1518" stroke-width="1.2"><rect x="4" y="3" width="11" height="23"/><rect x="15" y="10" width="8" height="16"/><path d="M7 7h2M11 7h2M7 11h2M11 11h2M7 15h2M11 15h2M7 19h2M11 19h2M18 14h2M18 18h2"/></svg>
    <div><div class="step-label">Step 2</div><div class="step-q">What industry are you in</div></div>
  </div>
  <div class="field" style="left:173px;top:284px;width:293px">Enter industry<svg viewBox="0 0 10 10"><rect x="2" y="1" width="6" height="8" fill="#999"/></svg></div>
  <div class="btn-next">NEXT <svg width="6" height="8" viewBox="0 0 6 8"><path d="M1 1l3 3-3 3" stroke="#fff" fill="none"/></svg></div>
  <div class="abs rule" style="top:392px"></div>
  <footer class="site-footer">
    <div class="brand"><div class="brand-mark"></div><div><div class="brand-name">TALL PINE</div><div class="brand-sub">GROWTH MARKETING</div></div></div>
    <div class="abs partner-badge" role="img" aria-label="Partner badge"><i></i><em></em></div>
    <div class="abs listing-badge" role="img" aria-label="Review listing badge"></div>
    <div class="abs follow">FOLLOW US</div>
    <div class="abs socials" aria-label="Social links"><i></i><i></i><i></i><i></i><i></i></div>
    <div class="abs rule" style="top:481px"></div>
    <div class="abs cols">
      <div class="col c1"><h4>QUICK LINKS</h4><p>About</p><p>Industries</p><p>Services</p><p>Resources</p><p>Training</p><p>Blog</p><p>Contact Us</p></div>
      <div class="col c2"><h4>SERVICES</h4><p>Programmatic Advertising</p><p>Search Engine Marketing (SEM)</p><p>Search Engine Optimization (SEO)</p><p>Content Marketing</p><p>Email Marketing</p><p>Paid Search Advertising</p><p>Paid Social Advertising</p></div>
      <div class="col c3"><h4>INDUSTRIES</h4><p>Ecommerce</p><p>Electricians</p><p>Financial Services Marketing</p><p>Home Builders</p><p>Home Services</p><p>Hvac Companies</p><p>Cosmetic Surgery Centers</p><p>Dental Marketing</p></div>
      <div class="col c4"><h4>GUIDES</h4><p>Ultimate Guide On Growing Your<br>Medical Practice Business</p><p>Legal Marketing Strategy Guide For<br>Law Firm Offices</p><p>Ultimate Story Ads Guide To<br>Skyrocket Your Leads And Sales</p><p>Ultimate Guide To Search<br>Engine Queries</p></div>
    </div>
    <div class="abs rule" style="top:715px"></div>
    <div class="abs copyright">Copyright © 2024 CompanyName &nbsp;All Rights Reserved. Privacy Policy, Terms Of Use, Press &amp; Media, Cookie Policy</div>
    <div class="abs build">x10</div>
  </footer>
</section>

<!-- Screen 3 -->
<section class="screen s3">
  <header class="site-header">
    <div class="brand"><div class="brand-mark"></div><div><div class="brand-name">TALL PINE</div><div class="brand-sub">GROWTH MARKETING</div></div></div>
    <div class="abs call">OR CALL US NOW : <b>(480) 555-0142</b></div>
    <div class="abs btn-orange">GROW YOUR REVENUE</div>
    <nav class="abs main-nav"><span>HOME</span><span>ABOUT</span><span>INDUSTRIES</span><span>SERVICES</span><span>BLOG</span><span>CONTACT US</span></nav>
  </header>
  <h1 class="abs form-title">GROW YOUR REVENUE NOW</h1>
  <div class="abs title-rule"></div>
  <svg class="abs stepper" width="711" height="34" viewBox="0 0 711 34" font-family="Poppins, sans-serif" font-size="13" font-weight="600" text-anchor="middle">
    <line x1="195" y1="17" x2="408" y2="17" stroke="#7d1518" stroke-width="2"/><line x1="408" y1="17" x2="516" y2="17" stroke="#ccc" stroke-width="1.2"/>
    <circle cx="178" cy="17" r="16.5" fill="#7d1518"/><text x="178" y="22" fill="#fff">1</text>
    <circle cx="267" cy="17" r="16.5" fill="#7d1518"/><text x="267" y="22" fill="#fff">2</text>
    <circle cx="356" cy="17" r="16.5" fill="#7d1518"/><text x="356" y="22" fill="#fff">3</text>
    <circle cx="444" cy="17" r="16" fill="#fff" stroke="#ccc" stroke-width="1.3"/><text x="444" y="22" fill="#bbb">4</text>
    <circle cx="533" cy="17" r="16" fill="#fff" stroke="#ccc" stroke-width="1.3"/><text x="533" y="22" fill="#bbb">5</text>
  </svg>
  <div class="abs step-head">
    <svg class="step-icon" viewBox="0 0 26 28" fill="none" stroke="#7d1518" stroke-width="1.2"><rect x="7" y="3" width="15" height="20" rx="1"/><path d="M10 8h9M10 12h9M10 16h6"/><circle cx="7" cy="21" r="5" fill="#fff"/><path d="M7 18v6"/></svg>
    <div><div class="step-label">Step 3</div><div class="step-q">What is your current advertising budget</div></div>
  </div>
  <div class="field" style="left:173px;top:284px;width:293px">Enter budget<span style="font-size:9px;color:#777">$</span></div>
  <div class="btn-next">NEXT <svg width="6" height="8" viewBox="0 0 6 8"><path d="M1 1l3 3-3 3" stroke="#fff" fill="none"/></svg></div>
  <div class="abs rule" style="top:392px"></div>
  <footer class="site-footer">
    <div class="brand"><div class="brand-mark"></div><div><div class="brand-name">TALL PINE</div><div class="brand-sub">GROWTH MARKETING</div></div></div>
    <div class="abs partner-badge" role="img" aria-label="Partner badge"><i></i><em></em></div>
    <div class="abs listing-badge" role="img" aria-label="Review listing badge"></div>
    <div class="abs follow">FOLLOW US</div>
    <div class="abs socials" aria-label="Social links"><i></i><i></i><i></i><i></i><i></i></div>
    <div class="abs rule" style="top:481px"></div>
    <div class="abs cols">
      <div class="col c1"><h4>QUICK LINKS</h4><p>About</p><p>Industries</p><p>Services</p><p>Resources</p><p>Training</p><p>Blog</p><p>Contact Us</p></div>
      <div class="col c2"><h4>SERVICES</h4><p>Programmatic Advertising</p><p>Search Engine Marketing (SEM)</p><p>Search Engine Optimization (SEO)</p><p>Content Marketing</p><p>Email Marketing</p><p>Paid Search Advertising</p><p>Paid Social Advertising</p></div>
      <div class="col c3"><h4>INDUSTRIES</h4><p>Ecommerce</p><p>Electricians</p><p>Financial Services Marketing</p><p>Home Builders</p><p>Home Services</p><p>Hvac Companies</p><p>Cosmetic Surgery Centers</p><p>Dental Marketing</p></div>
      <div class="col c4"><h4>GUIDES</h4><p>Ultimate Guide On Growing Your<br>Medical Practice Business</p><p>Legal Marketing Strategy Guide For<br>Law Firm Offices</p><p>Ultimate Story Ads Guide To<br>Skyrocket Your Leads And Sales</p><p>Ultimate Guide To Search<br>Engine Queries</p></div>
    </div>
    <div class="abs rule" style="top:715px"></div>
    <div class="abs copyright">Copyright © 2024 CompanyName &nbsp;All Rights Reserved. Privacy Policy, Terms Of Use, Press &amp; Media, Cookie Policy</div>
    <div class="abs build">x10</div>
  </footer>
</section>

<!-- Screen 4 -->
<section class="screen s4">
  <header class="site-header">
    <div class="brand"><div class="brand-mark"></div><div><div class="brand-name">TALL PINE</div><div class="brand-sub">GROWTH MARKETING</div></div></div>
    <div class="abs call">OR CALL US NOW : <b>(480) 555-0142</b></div>
    <div class="abs btn-orange">GROW YOUR REVENUE</div>
    <nav class="abs main-nav"><span>HOME</span><span>ABOUT</span><span>INDUSTRIES</span><span>SERVICES</span><span>BLOG</span><span>CONTACT US</span></nav>
  </header>
  <h1 class="abs form-title">GROW YOUR REVENUE NOW</h1>
  <div class="abs title-rule"></div>
  <svg class="abs stepper" width="711" height="34" viewBox="0 0 711 34" font-family="Poppins, sans-serif" font-size="13" font-weight="600" text-anchor="middle">
    <line x1="195" y1="17" x2="497" y2="17" stroke="#7d1518" stroke-width="2"/><line x1="497" y1="17" x2="516" y2="17" stroke="#ccc" stroke-width="1.2"/>
    <circle cx="178" cy="17" r="16.5" fill="#7d1518"/><text x="178" y="22" fill="#fff">1</text>
    <circle cx="267" cy="17" r="16.5" fill="#7d1518"/><text x="267" y="22" fill="#fff">2</text>
    <circle cx="356" cy="17" r="16.5" fill="#7d1518"/><text x="356" y="22" fill="#fff">3</text>
    <circle cx="444" cy="17" r="16.5" fill="#7d1518"/><text x="444" y="22" fill="#fff">4</text>
    <circle cx="533" cy="17" r="16" fill="#fff" stroke="#ccc" stroke-width="1.3"/><text x="533" y="22" fill="#bbb">5</text>
  </svg>
  <div class="abs step-head">
    <svg class="step-icon" viewBox="0 0 26 28" fill="none" stroke="#7d1518" stroke-width="1.2"><circle cx="13" cy="15" r="4"/><circle cx="13" cy="4" r="2.5"/><circle cx="3.5" cy="22" r="2.5"/><circle cx="22.5" cy="22" r="2.5"/><path d="M13 7v4M6 21l4-3M20 21l-4-3"/><path d="M5 10a10 10 0 0 1 4-5M21 10a10 10 0 0 0-4-5M8 25h10"/></svg>
    <div><div class="step-label">Step 4</div><div class="step-q">Do you have a CRM and if so what is it</div></div>
  </div>
  <div class="field" style="left:173px;top:284px;width:293px">Enter CRM details<svg viewBox="0 0 10 10"><circle cx="3" cy="4" r="1.5" fill="#999"/><circle cx="7" cy="4" r="1.5" fill="#999"/><rect x="1" y="6" width="8" height="3" rx="1.5" fill="#999"/></svg></div>
  <div class="btn-next">NEXT <svg width="6" height="8" viewBox="0 0 6 8"><path d="M1 1l3 3-3 3" stroke="#fff" fill="none"/></svg></div>
  <div class="abs rule" style="top:392px"></div>
  <footer class="site-footer">
    <div class="brand"><div class="brand-mark"></div><div><div class="brand-name">TALL PINE</div><div class="brand-sub">GROWTH MARKETING</div></div></div>
    <div class="abs partner-badge" role="img" aria-label="Partner badge"><i></i><em></em></div>
    <div class="abs listing-badge" role="img" aria-label="Review listing badge"></div>
    <div class="abs follow">FOLLOW US</div>
    <div class="abs socials" aria-label="Social links"><i></i><i></i><i></i><i></i><i></i></div>
    <div class="abs rule" style="top:481px"></div>
    <div class="abs cols">
      <div class="col c1"><h4>QUICK LINKS</h4><p>About</p><p>Industries</p><p>Services</p><p>Resources</p><p>Training</p><p>Blog</p><p>Contact Us</p></div>
      <div class="col c2"><h4>SERVICES</h4><p>Programmatic Advertising</p><p>Search Engine Marketing (SEM)</p><p>Search Engine Optimization (SEO)</p><p>Content Marketing</p><p>Email Marketing</p><p>Paid Search Advertising</p><p>Paid Social Advertising</p></div>
      <div class="col c3"><h4>INDUSTRIES</h4><p>Ecommerce</p><p>Electricians</p><p>Financial Services Marketing</p><p>Home Builders</p><p>Home Services</p><p>Hvac Companies</p><p>Cosmetic Surgery Centers</p><p>Dental Marketing</p></div>
      <div class="col c4"><h4>GUIDES</h4><p>Ultimate Guide On Growing Your<br>Medical Practice Business</p><p>Legal Marketing Strategy Guide For<br>Law Firm Offices</p><p>Ultimate Story Ads Guide To<br>Skyrocket Your Leads And Sales</p><p>Ultimate Guide To Search<br>Engine Queries</p></div>
    </div>
    <div class="abs rule" style="top:715px"></div>
    <div class="abs copyright">Copyright © 2024 CompanyName &nbsp;All Rights Reserved. Privacy Policy, Terms Of Use, Press &amp; Media, Cookie Policy</div>
    <div class="abs build">x10</div>
  </footer>
</section>

<!-- Screen 5 -->
<section class="screen s5">
  <header class="site-header">
    <div class="brand"><div class="brand-mark"></div><div><div class="brand-name">TALL PINE</div><div class="brand-sub">GROWTH MARKETING</div></div></div>
    <div class="abs call">OR CALL US NOW : <b>(480) 555-0142</b></div>
    <div class="abs btn-orange">GROW YOUR REVENUE</div>
    <nav class="abs main-nav"><span>HOME</span><span>ABOUT</span><span>INDUSTRIES</span><span>SERVICES</span><span>BLOG</span><span>CONTACT US</span></nav>
  </header>
  <h1 class="abs form-title">GROW YOUR REVENUE NOW</h1>
  <div class="abs title-rule"></div>
  <svg class="abs stepper" width="711" height="34" viewBox="0 0 711 34" font-family="Poppins, sans-serif" font-size="13" font-weight="600" text-anchor="middle">
    <line x1="195" y1="17" x2="516" y2="17" stroke="#7d1518" stroke-width="2"/>
    <circle cx="178" cy="17" r="16.5" fill="#7d1518"/><text x="178" y="22" fill="#fff">1</text>
    <circle cx="267" cy="17" r="16.5" fill="#7d1518"/><text x="267" y="22" fill="#fff">2</text>
    <circle cx="356" cy="17" r="16.5" fill="#7d1518"/><text x="356" y="22" fill="#fff">3</text>
    <circle cx="444" cy="17" r="16.5" fill="#7d1518"/><text x="444" y="22" fill="#fff">4</text>
    <circle cx="533" cy="17" r="16.5" fill="#7d1518"/><text x="533" y="22" fill="#fff">5</text>
  </svg>
  <div class="abs step-head">
    <svg class="step-icon" viewBox="0 0 26 28" fill="none" stroke="#7d1518" stroke-width="1.2"><rect x="3" y="2" width="20" height="24" rx="1"/><circle cx="10" cy="10" r="3"/><path d="M5 17a5 5 0 0 1 10 0M16 9h5M16 13h5M6 21h15"/></svg>
    <div><div class="step-label">Step 5</div><div class="step-q">What is your personal information</div></div>
  </div>
  <div class="field" style="left:173px;top:284px;width:136px">Name<svg viewBox="0 0 10 10"><circle cx="5" cy="3" r="2.2" fill="#999"/><rect x="1" y="6" width="8" height="4" rx="2" fill="#999"/></svg></div>
  <div class="field" style="left:324px;top:284px;width:141px">Phone<svg viewBox="0 0 10 10"><path d="M2 1l2 2-1 1.5a6 6 0 0 0 2.5 2.5L7 6l2 2-1.5 1.5C4 9 1 6 .5 2.5z" fill="#999"/></svg></div>
  <div class="field" style="left:173px;top:320px;width:292px">Email Address<svg viewBox="0 0 10 10"><rect x="0.5" y="2" width="9" height="6" fill="#999"/><path d="M.5 2l4.5 3.5L9.5 2" stroke="#fff" fill="none" stroke-width=".8"/></svg></div>
  <div class="btn-submit">SUBMIT <svg width="6" height="8" viewBox="0 0 6 8"><path d="M1 1l3 3-3 3" stroke="#fff" fill="none"/></svg></div>
  <div class="abs rule" style="top:392px"></div>
  <footer class="site-footer">
    <div class="brand"><div class="brand-mark"></div><div><div class="brand-name">TALL PINE</div><div class="brand-sub">GROWTH MARKETING</div></div></div>
    <div class="abs partner-badge" role="img" aria-label="Partner badge"><i></i><em></em></div>
    <div class="abs listing-badge" role="img" aria-label="Review listing badge"></div>
    <div class="abs follow">FOLLOW US</div>
    <div class="abs socials" aria-label="Social links"><i></i><i></i><i></i><i></i><i></i></div>
    <div class="abs rule" style="top:481px"></div>
    <div class="abs cols">
      <div class="col c1"><h4>QUICK LINKS</h4><p>About</p><p>Industries</p><p>Services</p><p>Resources</p><p>Training</p><p>Blog</p><p>Contact Us</p></div>
      <div class="col c2"><h4>SERVICES</h4><p>Programmatic Advertising</p><p>Search Engine Marketing (SEM)</p><p>Search Engine Optimization (SEO)</p><p>Content Marketing</p><p>Email Marketing</p><p>Paid Search Advertising</p><p>Paid Social Advertising</p></div>
      <div class="col c3"><h4>INDUSTRIES</h4><p>Ecommerce</p><p>Electricians</p><p>Financial Services Marketing</p><p>Home Builders</p><p>Home Services</p><p>Hvac Companies</p><p>Cosmetic Surgery Centers</p><p>Dental Marketing</p></div>
      <div class="col c4"><h4>GUIDES</h4><p>Ultimate Guide On Growing Your<br>Medical Practice Business</p><p>Legal Marketing Strategy Guide For<br>Law Firm Offices</p><p>Ultimate Story Ads Guide To<br>Skyrocket Your Leads And Sales</p><p>Ultimate Guide To Search<br>Engine Queries</p></div>
    </div>
    <div class="abs rule" style="top:715px"></div>
    <div class="abs copyright">Copyright © 2024 CompanyName &nbsp;All Rights Reserved. Privacy Policy, Terms Of Use, Press &amp; Media, Cookie Policy</div>
    <div class="abs build">x10</div>
  </footer>
</section>

</body>
</html>
```